Stylish new business card needed!

Hello everyone! I am in need of a new business card design for an alarm company here in Hurricane WV. I have all fonts, color codes and logos provided for you use! We are a young company and like the style of a clean sleek looking business card. Would like it double sided, one side holding the logo and the other with your design!
Target Market(s)
The people that are looking for the newest tech for home automation and security
Industry/Entity Type
Alarm services; Home automation
Contact Information for Business Card
Name of person; position (Sales; Installer); Phone Number (555.418.7260); Employee cell Number; Website (www.GuardedByVelk.example); Employee Email; Double sided
Look and feel
Each slider illustrates characteristics of the customer's brand and the style your logo design should communicate.

```html
<!DOCTYPE html>
<html lang="en">
<head>
<meta charset="utf-8">
<title>Velk Business Card</title>
<link href="https://fonts.googleapis.com/css2?family=Montserrat:wght@400;600;800&display=swap" rel="stylesheet">
<style>
  :root {
    --backdrop: #e6e6e6;
    --card: #2a2a2a;
    --edge: #e07a2e;
    --accent: #f08a3c;
    --ink: #f2f2f2;
    --muted: #cfcfcf;
  }
  * { box-sizing: border-box; margin: 0; padding: 0; }
  html, body {
    width: 1200px; height: 802px; overflow: hidden;
    background: var(--backdrop);
    font-family: "Montserrat", Arial, sans-serif;
  }
  .sheet {
    width: 1200px; height: 802px;
    display: flex; align-items: center; justify-content: center; gap: 60px;
  }
  .card {
    position: relative;
    width: 520px; height: 297px;
    background: var(--card);
    border-bottom: 4px solid var(--edge);
    box-shadow: 0 10px 24px rgba(0,0,0,0.18);
  }
  /* front */
  .card-front .brand {
    position: absolute; left: 64px; top: 52px;
  }
  .brand-name {
    display: flex; align-items: center; gap: 14px;
    font-size: 64px; font-weight: 400; letter-spacing: 4px;
    color: var(--ink); line-height: 1;
  }
  .brand-dot {
    width: 18px; height: 18px; border-radius: 50%; background: var(--accent);
  }
  .brand-tagline {
    margin-top: 10px;
    font-size: 10px; font-weight: 800; letter-spacing: 1px;
    text-transform: uppercase; color: var(--accent);
  }
  .details {
    position: absolute; left: 64px; bottom: 44px; right: 30px;
    display: flex; align-items: center;
  }
  .person { padding-right: 18px; }
  .person-name {
    font-size: 17px; font-weight: 600; text-transform: uppercase;
    color: var(--accent); letter-spacing: 0.5px;
  }
  .person-role { font-size: 13px; color: var(--ink); margin-top: 3px; }
  .divider { width: 1px; align-self: stretch; background: var(--muted); opacity: 0.6; }
  .contacts { list-style: none; padding-left: 16px; }
  .contacts li {
    display: flex; align-items: center; gap: 8px;
    font-size: 12px; color: var(--ink); line-height: 1.65;
  }
  .contacts svg { width: 11px; height: 11px; flex: none; }
  /* back */
  .card-back { display: flex; align-items: center; justify-content: center; }
  .card-back .brand-name { font-size: 96px; letter-spacing: 8px; gap: 20px; }
  .card-back .brand-dot { width: 26px; height: 26px; }
</style>
</head>
<body>
<main class="sheet">
  <section class="card card-front" aria-label="Card front">
    <div class="brand">
      <div class="brand-name"><span class="brand-dot"></span>VELK</div>
      <p class="brand-tagline">Automation and Security Services</p>
    </div>
    <div class="details">
      <div class="person">
        <p class="person-name">Marcus Hale</p>
        <p class="person-role">Sales / Installer</p>
      </div>
      <span class="divider"></span>
      <ul class="contacts">
        <li>
          <svg viewBox="0 0 12 12" aria-hidden="true"><path d="M2.5 1h2l1 3-1.3 1a6 6 0 0 0 2.8 2.8L8 6.5l3 1v2c0 .8-.7 1.5-1.5 1.5A9 9 0 0 1 1 2.5C1 1.7 1.7 1 2.5 1z" fill="var(--accent)"/></svg>
          555.418.7260
        </li>
        <li>
          <svg viewBox="0 0 12 12" aria-hidden="true"><rect x="1" y="2.5" width="10" height="7" fill="none" stroke="var(--accent)" stroke-width="1.2"/><path d="M1 2.5l5 4 5-4" fill="none" stroke="var(--accent)" stroke-width="1.2"/></svg>
          info@GuardedByVelk.example
        </li>
        <li>
          <svg viewBox="0 0 12 12" aria-hidden="true"><circle cx="6" cy="6" r="5" fill="none" stroke="var(--accent)" stroke-width="1.1"/><ellipse cx="6" cy="6" rx="2.2" ry="5" fill="none" stroke="var(--accent)" stroke-width="1"/><path d="M1 6h10" stroke="var(--accent)" stroke-width="1"/></svg>
          www.GuardedByVelk.example
        </li>
      </ul>
    </div>
  </section>

  <section class="card card-back" aria-label="Card back">
    <div class="brand-name"><span class="brand-dot"></span>VELK</div>
  </section>
</main>
</body>
</html>
```